Business Card Design

- one on one personal training
- group personal training
- indoor or outdoor training available
- fitness and health assessments
- personalised fitness programs
- flexible hours for training

I am a Personal Trainer in Perth Australia. I am looking to expand my word of mouth client base.

I would like to see something that uses the colours blue, green and/or yellow.

The final design should reflect the way that I train clients, fun, motivating and perhaps a little quirky?
Updates

update with a logo with the letters MVF thank you

Hi all, Have had some great designs so far. Have decided to go double sided, perhaps to use the back to list my services. Thank you

Please check update brief. Thank you.

Target Market(s)

Professionals, ages 30 to 60

Industry/Entity Type

Training

Contact Information for Business Card

Marla Prentiss
Personal Trainer

0412 807 254
marlafitcoach@quellmail.example
http://www.marlafitcoach.example

Requirements
Must have
• A logo with the letter MVF
Nice to have
• a logo to represent either; fitness, health, change, overall well-being.
Should not have
• Please no weights or lotus flowers!!

```html
<!DOCTYPE html>
<html lang="en">
<head>
<meta charset="utf-8">
<title>Marla Prentiss – Personal Trainer Business Cards</title>
<link rel="stylesheet" href="https://fonts.googleapis.com/css2?family=Open+Sans:wght@400;600;700&family=Roboto+Condensed:ital,wght@1,700&display=swap">
<style>
  :root {
    --stage: #e8e7e3;
    --card: #ffffff;
    --blue: #1f6fb8;
    --green: #3aa845;
    --lime: #8cc63f;
    --yellow: #f6c918;
    --orange: #f39a1e;
    --red: #e2412f;
    --ink: #4a4a4a;
    --muted: #7a7a7a;
  }
  * { box-sizing: border-box; margin: 0; padding: 0; }
  html, body { width: 1200px; height: 872px; overflow: hidden; }
  body {
    background: var(--stage);
    font-family: "Open Sans", Arial, sans-serif;
    color: var(--ink);
    position: relative;
  }
  .card {
    position: absolute;
    width: 520px;
    height: 318px;
    background: var(--card);
    box-shadow: 0 2px 10px rgba(0,0,0,.12);
    overflow: hidden;
  }
  .card--front { left: 50px; top: 250px; }
  .card--back { left: 630px; top: 250px; }

  .name {
    font-family: "Roboto Condensed", "Arial Narrow", sans-serif;
    font-style: italic;
    font-weight: 700;
    color: var(--blue);
    font-size: 30px;
    line-height: 1;
    white-space: nowrap;
  }
  .role { font-size: 12px; color: var(--muted); margin-top: 4px; }
  .contact { font-size: 11px; line-height: 1.65; color: var(--ink); white-space: nowrap; }

  .brand {
    font-family: "Open Sans", Arial, sans-serif;
    font-weight: 700;
    color: var(--blue);
    display: flex;
    align-items: center;
    gap: 6px;
    line-height: 1;
  }
  .brand__dot { width: 12px; height: 12px; border-radius: 50%; background: var(--green); flex: none; }

  .services { list-style: none; font-size: 11px; line-height: 1.75; color: var(--ink); white-space: nowrap; }
  .services li { display: flex; align-items: center; gap: 8px; }
  .services li::before {
    content: ""; width: 7px; height: 7px; flex: none; background: var(--bullet);
  }
  .services li:nth-child(1) { --bullet: var(--blue); }
  .services li:nth-child(2) { --bullet: var(--green); }
  .services li:nth-child(3) { --bullet: var(--yellow); }
  .services li:nth-child(4) { --bullet: var(--orange); }
  .services li:nth-child(5) { --bullet: var(--lime); }
  .services li:nth-child(6) { --bullet: var(--red); }

  /* front */
  .front__identity { position: absolute; left: 34px; top: 34px; }
  .front__brand { position: absolute; right: 34px; top: 40px; font-size: 24px; }
  .front__contact { position: absolute; left: 34px; top: 112px; }
  .front__art {
    position: absolute; right: 0; bottom: 0; width: 210px; height: 190px;
    background: linear-gradient(135deg, var(--yellow) 0%, var(--yellow) 38%, var(--green) 62%, var(--blue) 100%);
  }
  .front__services { position: absolute; left: 34px; bottom: 24px; }

  /* back */
  .back__ribbon { position: absolute; left: 0; top: 0; width: 520px; height: 318px; }
  .back__contact { position: absolute; left: 40px; top: 30px; }
  .back__identity { position: absolute; left: 40px; top: 118px; }
  .back__brand { position: absolute; left: 250px; top: 124px; font-size: 24px; }
  .back__services { position: absolute; left: 40px; top: 180px; }

  .logo-panel {
    position: absolute; left: 900px; top: 636px; width: 180px; height: 180px;
    background: var(--card);
    display: flex; align-items: center; justify-content: center;
    box-shadow: 0 2px 10px rgba(0,0,0,.1);
  }
  .logo-panel .brand { font-size: 44px; }
</style>
</head>
<body>

  <section class="card card--front" aria-label="Business card front">
    <div class="front__identity">
      <p class="name">Marla Prentiss</p>
      <p class="role">Personal Trainer</p>
    </div>
    <div class="brand front__brand"><span class="brand__dot"></span>MVF</div>
    <div class="front__contact contact">
      <p>Phone: 0412 807 254</p>
      <p>Email: marlafitcoach@quellmail.example</p>
      <p>Website: http://www.marlafitcoach.example</p>
    </div>
    <div class="front__art" role="img" aria-label="Bright yellow, green and blue illustration of an active trainer in motion"></div>
    <ul class="services front__services">
      <li>One on one personal training</li>
      <li>Group personal training</li>
      <li>Indoor or outdoor training available</li>
      <li>Fitness and health assessments</li>
      <li>Personalised fitness programs</li>
    </ul>
  </section>

  <section class="card card--back" aria-label="Business card back">
    <svg class="back__ribbon" viewBox="0 0 520 318" role="img" aria-label="Flowing ribbons in blue, green, yellow, orange and red">
      <defs>
        <linearGradient id="ribbon-tones" x1="0" y1="0" x2="1" y2="1">
          <stop offset="0" stop-color="#1f6fb8"/>
          <stop offset=".3" stop-color="#3aa845"/>
          <stop offset=".55" stop-color="#f6c918"/>
          <stop offset=".8" stop-color="#f39a1e"/>
          <stop offset="1" stop-color="#e2412f"/>
        </linearGradient>
      </defs>
      <path d="M330 0 C 380 60, 420 90, 440 160 S 470 270, 520 318 L 520 0 Z" fill="url(#ribbon-tones)" opacity=".85"/>
    </svg>
    <div class="back__contact contact">
      <p>Phone: 0412 807 254</p>
      <p>Email: marlafitcoach@quellmail.example</p>
      <p>Website: http://www.marlafitcoach.example</p>
    </div>
    <div class="back__identity">
      <p class="name">Marla Prentiss</p>
      <p class="role">Personal Trainer</p>
    </div>
    <div class="brand back__brand"><span class="brand__dot"></span>MVF</div>
    <ul class="services back__services">
      <li>One on one personal training</li>
      <li>Group personal training</li>
      <li>Indoor or outdoor training available</li>
      <li>Fitness and health assessments</li>
      <li>Personalised fitness programs</li>
      <li>Flexible hours for training</li>
    </ul>
  </section>

  <aside class="logo-panel" aria-label="Logo">
    <div class="brand"><span class="brand__dot"></span>MVF</div>
  </aside>

</body>
</html>
```